Tandem Hearth Works Pty Ltd

We need business cards for a company based in Perth, we install, service and maintain fire equipment.
On the front we want a great design with our logo and a small spot for our full company name, general company email address and office number. On the back we need space for our name, title, mobile number and email address on the back.

Target Market(s)

Facility managers and commercial/industrial building owners/occupiers.

Contact Information for Business Card

Font styles to use
Sans Serif

Requirements
Must have
• Please only submit 5 of your best samples.
Darker tones are preferred.
Nice to have
• We want to use, black, red and grey. Keep it modern and clean.
I've attached the company logo and a sample of a boarder we use on our emergency plans.
Should not have
• No preference. Let the designer choose.

```html
<!DOCTYPE html>
<html lang="en">
<head>
<meta charset="utf-8">
<title>Tandem Hearth Works – Business Cards</title>
<link rel="stylesheet" href="https://fonts.googleapis.com/css2?family=Montserrat:wght@400;600;800&family=Roboto:wght@300;400&display=swap">
<style>
  :root {
    --stage: #3a3a3d;
    --card: #0c0c0d;
    --card-edge: #151516;
    --red: #ed1c24;
    --white: #f2f2f2;
    --grey: #3b3b3d;
    --grey-soft: #55555a;
  }
  * { box-sizing: border-box; margin: 0; padding: 0; }
  html, body { width: 1200px; height: 1200px; overflow: hidden; }
  body {
    background: var(--stage);
    display: flex;
    flex-direction: column;
    align-items: center;
    justify-content: center;
    gap: 50px;
    font-family: "Roboto", sans-serif;
  }
  .card {
    position: relative;
    width: 860px;
    height: 490px;
    border-radius: 28px;
    background: linear-gradient(160deg, var(--card-edge), var(--card) 60%);
    box-shadow: 0 24px 50px rgba(0,0,0,.55);
    overflow: hidden;
  }

  /* Front */
  .card-front .mark {
    position: absolute;
    top: 150px; left: 0; right: 0;
    text-align: center;
    font-family: "Montserrat", sans-serif;
    font-weight: 800;
    font-size: 86px;
    letter-spacing: -1px;
    color: var(--grey);
  }
  .card-front .details {
    position: absolute;
    bottom: 70px; left: 0; right: 0;
    text-align: center;
    color: var(--grey-soft);
    font-size: 18px;
    line-height: 1.5;
  }
  .card-front .details .dot {
    display: inline-block;
    width: 7px; height: 7px;
    border-radius: 50%;
    background: var(--red);
    vertical-align: middle;
    margin: 0 8px;
  }

  /* Back */
  .card-back .identity {
    position: absolute;
    top: 110px; left: 70px;
  }
  .card-back .name {
    font-family: "Montserrat", sans-serif;
    font-weight: 600;
    font-size: 28px;
    letter-spacing: 5px;
    color: var(--red);
  }
  .card-back .role {
    font-family: "Montserrat", sans-serif;
    font-size: 15px;
    letter-spacing: 4px;
    color: var(--white);
    margin-top: 6px;
  }
  .card-back .rule {
    width: 70px; height: 2px;
    background: var(--red);
    margin: 18px 0 20px;
  }
  .card-back .contact { list-style: none; }
  .card-back .contact li {
    display: flex;
    align-items: center;
    gap: 14px;
    color: var(--white);
    font-size: 19px;
    letter-spacing: 2px;
    margin-bottom: 12px;
  }
  .card-back .contact svg { width: 16px; height: 16px; flex: none; }
  .card-back .mark {
    position: absolute;
    right: 60px; bottom: 60px;
    text-align: right;
    font-family: "Montserrat", sans-serif;
    font-weight: 800;
    font-size: 92px;
    line-height: .95;
    color: var(--red);
  }
</style>
</head>
<body>

<section class="card card-front">
  <div class="mark">Tandem Hearth</div>
  <div class="details">
    <div><span class="dot"></span>Tandem Hearth Works Pty Ltd<span class="dot"></span></div>
    <div>123 456 7890 | youremail.com</div>
  </div>
</section>

<section class="card card-back">
  <div class="identity">
    <div class="name">MARCUS VALE</div>
    <div class="role">FOUNDER &amp; CEO</div>
    <div class="rule"></div>
    <ul class="contact">
      <li>
        <svg viewBox="0 0 16 16" aria-hidden="true"><path fill="#ed1c24" d="M3.5 1.5l2.5 0 1 3.5-1.6 1.2a8 8 0 0 0 4.4 4.4L11 9l3.5 1v2.5c0 1-.8 1.5-1.5 1.5C6.8 14 2 9.2 2 3c0-.7.5-1.5 1.5-1.5z"/></svg>
        +61 400 555 017
      </li>
      <li>
        <svg viewBox="0 0 16 16" aria-hidden="true"><rect x="1.5" y="3.5" width="13" height="9" fill="none" stroke="#ed1c24" stroke-width="1.5"/><path d="M1.5 3.5l6.5 5 6.5-5" fill="none" stroke="#ed1c24" stroke-width="1.5"/></svg>
        ceo@tandemhearth.com
      </li>
      <li>
        <svg viewBox="0 0 16 16" aria-hidden="true"><circle cx="8" cy="8" r="6.3" fill="none" stroke="#ed1c24" stroke-width="1.4"/><ellipse cx="8" cy="8" rx="2.8" ry="6.3" fill="none" stroke="#ed1c24" stroke-width="1.2"/><path d="M1.7 8h12.6" stroke="#ed1c24" stroke-width="1.2"/></svg>
        www.tandemhearth.com
      </li>
    </ul>
  </div>
  <div class="mark">Tandem<br>Hearth</div>
</section>

</body>
</html>
```